K7 Services business card design contest. Use logo and create a professional layout.

See attached sample. Please sharpen all text and images, don't want any pix-elated content. We are looking for a clean look that quickly provides the information need. Please include our information provided on the sample card. Please feel free to offer any design changes. Please only user the colors provided: #2D3539 & #FFA500. Do not prefer any images other than the K7 Logo

Target Market(s)

Construction, Architects, General Contractors, residential

Industry/Entity Type

Business

Contact Information for Business Card

Company logo, Name, email, fax & phone

Font styles to use
Other font styles liked:
• Josefin Slab

Requirements
Must have
• Name
• Phone & Fax #'s
• address
• Logo
• Website url: www.kq7services.example
Nice to have
• Font Colors #2D3539 & #FFA400
• We prefer a white background.

```html
<!DOCTYPE html>
<html lang="en">
<head>
<meta charset="utf-8">
<title>K7 Services – Business Card</title>
<link rel="stylesheet" href="https://fonts.googleapis.com/css2?family=Ubuntu:wght@400;500;700&display=swap">
<style>
  :root {
    --backdrop: #a6a7aa;
    --card: #ffffff;
    --ink: #2D3539;
    --text-dark: #2D3539;
    --accent: #FFA500;
    --on-dark: #ffffff;
  }
  * { margin: 0; padding: 0; box-sizing: border-box; }
  html, body {
    width: 1200px;
    height: 829px;
    overflow: hidden;
  }
  body {
    background: var(--backdrop);
    font-family: "Ubuntu", Arial, sans-serif;
    position: relative;
  }
  .card {
    position: absolute;
    left: 184px;
    top: 178px;
    width: 819px;
    height: 468px;
    background: var(--card);
    overflow: hidden;
    box-shadow: 2px 3px 4px rgba(0, 0, 0, 0.35);
  }
  .card__band {
    position: absolute;
    inset: 0;
    width: 100%;
    height: 100%;
  }
  .card__band path { fill: var(--ink); }

  .brand {
    position: absolute;
    left: 41px;
    top: 56px;
    font-size: 50px;
    font-weight: 500;
    color: var(--ink);
    letter-spacing: -0.5px;
    line-height: 1;
  }

  .person {
    position: absolute;
    left: 41px;
    top: 212px;
  }
  .person__name {
    font-size: 31px;
    font-weight: 400;
    color: var(--accent);
    line-height: 1;
  }
  .person__title {
    margin-top: 9px;
    font-size: 20px;
    font-weight: 400;
    color: var(--text-dark);
    line-height: 1;
  }

  .services {
    position: absolute;
    right: 47px;
    top: 122px;
    list-style: none;
    text-align: right;
    font-size: 34px;
    font-weight: 700;
    color: var(--accent);
    line-height: 53px;
  }

  .contact {
    position: absolute;
    right: 47px;
    top: 324px;
    color: var(--on-dark);
    font-size: 18px;
    line-height: 24px;
    text-align: right;
  }
  .contact__phones {
    display: inline-grid;
    grid-template-columns: auto auto auto;
    column-gap: 8px;
    text-align: left;
  }
  .contact__label { font-weight: 700; }
  .contact__address {
    margin-top: 8px;
    font-style: normal;
  }
  .contact__web {
    margin-top: 2px;
    color: var(--accent);
    font-weight: 500;
  }
</style>
</head>
<body>
  <main class="card">
    <svg class="card__band" viewBox="0 0 683 390" preserveAspectRatio="none" aria-hidden="true">
      <path d="M537 0 L683 0 L683 390 L90 390 C96 330 128 302 180 296 L404 265 L487 58 C500 24 514 4 537 0 Z"/>
    </svg>

    <div class="brand">K7 Services</div>

    <div class="person">
      <p class="person__name">Daniel R. Hollis, MBA</p>
      <p class="person__title">Director of Operations</p>
    </div>

    <ul class="services">
      <li>Dron</li>
      <li>Webcam</li>
      <li>Video</li>
    </ul>

    <div class="contact">
      <div class="contact__phones">
        <span class="contact__label">Mobile</span><span class="contact__label">:</span><span>(555) 014 - 2093</span>
        <span class="contact__label">Fax</span><span class="contact__label">:</span><span>(555) 018 - 4072</span>
      </div>
      <address class="contact__address">
        2710 Larkspur Road, Suit 410-218<br>
        Millbrook, Georgia, 30099
      </address>
      <p class="contact__web">www.kq7services.example</p>
    </div>
  </main>
</body>
</html>
```